lum-vex needs updated company presentation for perspective principals

We are looking to update our current company overview presentation that we use for giving new and prospective principals (companies we see for) an overview of our company and our capabilities. We have a PowerPoint presentation but would like to give it a more professional and updated look. There are some modification we'd like to incorporate into the new presentation, but that can be added later.
We will also be looking at using this look to update our website and some additional promotion literature for the near future ( Brochures, Mailers....)
Updates

On the territory overview. I need to increase the state view to include Missouri, Iowa, Kansas, Nebraska, Minnesota and Tennessee. This is the first project we've worked on, so please let me know what additional information is required or makes this process go smoother.

Industry/Entity Type

Chemical Product

Font styles to use
Serif

Colors
ec1f27
000000

Requirements
Must have
• Company History, Territory overview, Industries Served, Principal Represented, Employee overview, Historic Performance

```html
<!DOCTYPE html>
<html lang="en">
<head>
<meta charset="utf-8">
<title>lum-vex, inc. — Company Presentation</title>
<link href="https://fonts.googleapis.com/css2?family=Open+Sans:wght@300;400;700;800&family=Roboto+Condensed:wght@700&display=swap" rel="stylesheet">
<style>
  :root{
    --red:#c10a16;
    --brand-red:#ec1f27;
    --charcoal:#444446;
    --header-gray:#58585a;
    --paper:#f7f7f8;
    --ink:#333;
    --muted:#666;
    --icon:#c9cacd;
    --step1:#d2d2d7;
    --step2:#b4b4b9;
    --step3:#6e6d72;
  }
  *{margin:0;padding:0;box-sizing:border-box}
  html,body{width:1200px;height:1200px;overflow:hidden}
  body{background:linear-gradient(180deg,#7b7b7b,#6b6b6b);font-family:"Open Sans",sans-serif;position:relative}
  .slide{position:absolute;overflow:hidden;background:var(--paper)}
  .abs{position:absolute}
  .logo{position:absolute;font-family:"Open Sans",sans-serif;font-weight:800;color:var(--brand-red);letter-spacing:-.5px;white-space:nowrap;line-height:1}
  .badge{position:absolute;border-radius:50%;background:#fff;border:3px solid #8a8a8c}
  .slide-header{position:absolute;left:0;top:0;width:100%;height:50px;background:var(--header-gray)}
  .slide-title{position:absolute;left:30px;top:11px;color:#fff;font-weight:400;font-size:21px}
  .slide-num{position:absolute;top:0;right:0;width:109px;height:50px;background:var(--red);color:#3a0808;font-size:28px;font-weight:300;text-align:center;line-height:50px}
  .body-copy{position:absolute;font-size:6.6px;line-height:9px;color:var(--ink);text-align:center}
  .caption{position:absolute;font-size:5.4px;line-height:7.4px;color:var(--muted);width:100px}
  .tiny{font-size:4.3px;line-height:5.8px}
</style>
</head>
<body>

<!-- Cover -->
<section class="slide cover" style="left:51px;top:144px;width:539px;height:303px;background:#fff">
  <div class="abs" style="left:0;top:0;width:100%;height:97px;background:var(--charcoal)"></div>
  <div class="logo" style="left:80px;top:42px;font-size:26px">lum-vex, inc.</div>
  <div class="abs" style="left:0;top:97px;width:100%;height:97px;background:var(--red)"></div>
  <div class="abs" style="left:0;top:194px;width:100%;height:4px;background:var(--charcoal)"></div>
  <p class="abs" style="left:76px;top:140px;color:#fff;font-family:'Roboto Condensed',sans-serif;font-weight:700;font-size:13px">Representing the World's Best</p>
  <div class="badge" style="left:455px;top:122px;width:52px;height:52px;border-color:#fff;background:var(--red);box-shadow:0 0 0 2px #fff inset"></div>
  <p class="body-copy" style="left:85px;top:250px;width:370px">Lorem ipsum dolor sit amet, ius exerci corpora eu. Per ne meis vocent iudicabit, in oratio graeci atomorum vim, vide habemus docendi ut eam. Cu dolor salutatus efficiendi nam. Debet quaeque nec te. Omittam reprehendunt eu mea, vocent aperiri eum et, ut ius summo dignissim. Pro ne ubique voluptaria, te alia lorem perfecto vix.</p>
</section>

<!-- Company History -->
<section class="slide history" style="left:615px;top:144px;width:540px;height:303px">
  <header class="slide-header"><h2 class="slide-title">Company History</h2><div class="slide-num">01</div></header>
  <div class="badge" style="left:380px;top:5px;width:40px;height:40px"></div>

  <svg class="abs" style="left:42px;top:90px" width="44" height="44" viewBox="0 0 44 44" role="img" aria-label="Bar chart icon">
    <rect x="0" y="20" width="11" height="24" fill="var(--icon)"/><rect x="15" y="10" width="11" height="34" fill="var(--icon)"/><rect x="30" y="0" width="11" height="44" fill="var(--icon)"/>
  </svg>
  <p class="caption" style="left:42px;top:140px">Lorem ipsum dolor sit amet, dicit melius consetetur ut eum, vim probo libris dicunt at.</p>

  <svg class="abs" style="left:177px;top:90px" width="44" height="44" viewBox="0 0 44 44" role="img" aria-label="Gear icon">
    <circle cx="22" cy="22" r="17" fill="none" stroke="var(--icon)" stroke-width="8" stroke-dasharray="6 4.7"/>
    <circle cx="22" cy="22" r="13" fill="none" stroke="var(--icon)" stroke-width="7"/>
  </svg>
  <p class="caption" style="left:177px;top:140px">Lorem ipsum dolor sit amet, dicit melius consetetur ut eum, vim probo libris dicunt at.</p>

  <svg class="abs" style="left:44px;top:190px" width="48" height="44" viewBox="0 0 48 44" role="img" aria-label="User icon">
    <circle cx="24" cy="13" r="12" fill="var(--icon)"/><path d="M0 44 Q0 26 24 26 Q48 26 48 44Z" fill="var(--icon)"/>
  </svg>
  <p class="caption" style="left:42px;top:240px">Lorem ipsum dolor sit amet, dicit melius consetetur ut eum, vim probo libris dicunt at.</p>

  <svg class="abs" style="left:177px;top:190px" width="44" height="44" viewBox="0 0 44 44" role="img" aria-label="Search icon">
    <circle cx="17" cy="17" r="13" fill="none" stroke="var(--icon)" stroke-width="6"/><line x1="27" y1="27" x2="41" y2="41" stroke="var(--icon)" stroke-width="7" stroke-linecap="round"/>
  </svg>
  <p class="caption" style="left:177px;top:240px">Lorem ipsum dolor sit amet, dicit melius consetetur ut eum, vim probo libris dicunt at.</p>

  <div class="abs" style="left:336px;top:70px;width:1px;height:220px;background:#ddd"></div>
  <h3 class="abs" style="left:362px;top:92px;font-weight:400;font-size:24px;color:#222">HEADLINE</h3>
  <p class="abs" style="left:362px;top:121px;font-size:7.5px;color:#444">Lorem Ipsum Dolor Sit Amet</p>
  <p class="abs tiny" style="left:362px;top:153px;width:160px;color:#555">Lorem ipsum dolor sit amet, ius exerci corpora eu. Per ne meis vocent iudicabit, in oratio graeci atomorum vim, vide habemus docendi ut eam. Cu dolor salutatus efficiendi nam.</p>
  <p class="abs tiny" style="left:362px;top:201px;width:160px;color:#555">Nam dolor latine ornatus id, choro partiendo mei et. Idque facer vidisse id nec, constituam dissentiunt per ex. In nam elitr assueverit.</p>
  <div class="logo" style="left:374px;top:265px;font-size:19px">lum-vex, inc.</div>
</section>

<!-- Territory overview -->
<section class="slide territory" style="left:51px;top:473px;width:539px;height:302px">
  <header class="slide-header"><h2 class="slide-title" style="left:50px">Territory overview</h2><div class="slide-num" style="width:110px">02</div></header>
  <div class="badge" style="left:381px;top:5px;width:40px;height:40px"></div>
  <svg class="abs" style="left:84px;top:90px" width="371" height="123" viewBox="0 0 371 123" aria-label="Three step process">
    <path d="M5 0 H123 L123 55 L129 61 L123 67 V123 H5 Q0 123 0 118 V5 Q0 0 5 0Z" fill="var(--step1)"/>
    <path d="M123 0 H247 V55 L253 61 L247 67 V123 H123 V67 L129 61 L123 55Z" fill="var(--step2)"/>
    <path d="M247 0 H366 Q371 0 371 5 V118 Q371 123 366 123 H247 V67 L253 61 L247 55Z" fill="var(--step3)"/>
    <g fill="#fff" font-family="Open Sans, sans-serif" font-weight="300" font-size="18" text-anchor="middle">
      <text x="62" y="44">STEP 1</text><text x="186" y="44">STEP 2</text><text x="309" y="44">STEP 3</text>
    </g>
  </svg>
  <p class="abs" style="left:97px;top:146px;width:98px;font-size:3.6px;line-height:4.8px;color:#fff;text-align:center">Lorem ipsum dolor sit amet, ius exerci corpora eu. Per ne meis vocent iudicabit, vide habemus docendi.</p>
  <p class="abs" style="left:221px;top:146px;width:98px;font-size:3.6px;line-height:4.8px;color:#fff;text-align:center">Lorem ipsum dolor sit amet, ius exerci corpora eu. Per ne meis vocent iudicabit, vide habemus docendi.</p>
  <p class="abs" style="left:344px;top:146px;width:98px;font-size:3.6px;line-height:4.8px;color:#fff;text-align:center">Lorem ipsum dolor sit amet, ius exerci corpora eu. Per ne meis vocent iudicabit, vide habemus docendi.</p>
  <p class="body-copy" style="left:85px;top:229px;width:370px">Lorem ipsum dolor sit amet, ius exerci corpora eu. Per ne meis vocent iudicabit, in oratio graeci atomorum vim, vide habemus docendi ut eam. Cu dolor salutatus efficiendi nam. Debet quaeque nec te. Omittam reprehendunt eu mea, vocent aperiri eum et, ut ius summo dignissim. Pro ne ubique voluptaria, te alia lorem perfecto vix.</p>
  <div class="logo" style="left:375px;top:270px;font-size:19px">lum-vex, inc.</div>
</section>

<!-- Industries Served -->
<section class="slide industries" style="left:615px;top:473px;width:540px;height:302px">
  <header class="slide-header"><h2 class="slide-title" style="left:26px">Industries Served</h2><div class="slide-num">03</div></header>
  <div class="badge" style="left:384px;top:5px;width:40px;height:40px"></div>
  <svg class="abs" style="left:0;top:0" width="540" height="302" viewBox="0 0 540 302" role="img" aria-label="Area chart of industries served, A to L">
    <g stroke="#cfcfcf" stroke-width=".6" stroke-dasharray="2 2">
      <line x1="85" y1="87" x2="479" y2="87"/><line x1="85" y1="118" x2="479" y2="118"/><line x1="85" y1="150" x2="479" y2="150"/><line x1="85" y1="181" x2="479" y2="181"/>
      <line x1="85" y1="87" x2="85" y2="212"/><line x1="121" y1="87" x2="121" y2="212"/><line x1="157" y1="87" x2="157" y2="212"/><line x1="192" y1="87" x2="192" y2="212"/><line x1="228" y1="87" x2="228" y2="212"/><line x1="264" y1="87" x2="264" y2="212"/><line x1="300" y1="87" x2="300" y2="212"/><line x1="336" y1="87" x2="336" y2="212"/><line x1="371" y1="87" x2="371" y2="212"/><line x1="407" y1="87" x2="407" y2="212"/><line x1="443" y1="87" x2="443" y2="212"/><line x1="479" y1="87" x2="479" y2="212"/>
    </g>
    <path d="M85 165 L120.8 143.1 L156.6 160.4 L192.4 149.4 L228.2 138.4 L264 157.2 L299.8 165 L335.6 155.7 L371.4 136.9 L407.2 118.1 L443 130.6 L478.8 107.1 V212 H85Z" fill="#c4343b"/>
    <line x1="85" y1="212" x2="479" y2="212" stroke="#999" stroke-width=".6"/>
    <g font-family="Open Sans, sans-serif" font-size="7" fill="#333">
      <text x="60" y="90">400</text><text x="60" y="121">300</text><text x="60" y="153">200</text><text x="62" y="184">100</text>
      <g text-anchor="middle"><text x="85" y="225">A</text><text x="121" y="225">B</text><text x="157" y="225">C</text><text x="192" y="225">D</text><text x="228" y="225">E</text><text x="264" y="225">F</text><text x="300" y="225">G</text><text x="336" y="225">H</text><text x="371" y="225">I</text><text x="407" y="225">J</text><text x="443" y="225">K</text><text x="479" y="225">L</text></g>
    </g>
    <path d="M138 126 H175 V145 H162 L156.6 151 L151 145 H138Z" fill="#b50a14"/>
    <path d="M282 131 H318 V150 H305 L299.8 156 L294 150 H282Z" fill="#e54a4e"/>
    <path d="M389 82 H426 V101 H413 L407.2 107 L401 101 H389Z" fill="#dcdcde"/>
    <circle cx="156.6" cy="160.4" r="2.5" fill="#777"/><circle cx="299.8" cy="165" r="2.5" fill="#777"/><circle cx="407.2" cy="118.1" r="2.5" fill="#777"/>
    <rect x="78" y="241" width="16" height="16" fill="#b50a14"/><rect x="196" y="241" width="16" height="16" fill="#e54a4e"/><rect x="314" y="241" width="16" height="16" fill="#dcdcde"/>
  </svg>
  <p class="abs" style="left:99px;top:241px;width:90px;font-size:4.3px;line-height:5.8px;color:#555">Lorem ipsum dolor sit amet, dicit melius consetetur ut eum, vim probo libris dicunt at.</p>
  <p class="abs" style="left:217px;top:241px;width:90px;font-size:4.3px;line-height:5.8px;color:#555">Lorem ipsum dolor sit amet, dicit melius consetetur ut eum, vim probo libris dicunt at.</p>
  <p class="abs" style="left:335px;top:241px;width:90px;font-size:4.3px;line-height:5.8px;color:#555">Lorem ipsum dolor sit amet, dicit melius consetetur ut eum, vim probo libris dicunt at.</p>
  <div class="logo" style="left:378px;top:270px;font-size:19px">lum-vex, inc.</div>
</section>

<!-- Principal Represented -->
<section class="slide principals" style="left:51px;top:801px;width:539px;height:303px;background:var(--header-gray)">
  <div class="abs" style="left:0;top:0;width:270px;height:100%;background:var(--red)"></div>
  <h2 class="abs" style="left:50px;top:12px;color:#fff;font-weight:400;font-size:21px">Principal Represented</h2>
  <div class="badge" style="left:482px;top:9px;width:40px;height:40px"></div>

  <h3 class="abs" style="left:0;top:61px;width:270px;text-align:center;font-weight:400;font-size:28px;letter-spacing:7px;color:#3a0808">OPTION A</h3>
  <p class="abs" style="left:0;top:97px;width:270px;text-align:center;font-size:7.5px;color:#4a0a0a">Lorem Ipsum Dolor Sit Amet</p>
  <div class="abs" style="left:85px;top:109px;width:100px;height:1px;background:#4a0a0a"></div>
  <p class="abs tiny" style="left:48px;top:129px;width:176px;text-align:center;color:#5a0a0a">Lorem ipsum dolor sit amet, ius exerci corpora eu. Per ne meis vocent iudicabit, in oratio graeci atomorum vim, vide habemus docendi ut eam. Cu dolor salutatus efficiendi nam.</p>
  <p class="abs tiny" style="left:48px;top:183px;width:176px;text-align:center;color:#5a0a0a">Nam dolor latine ornatus id, choro partiendo mei et. Idque facer vidisse id nec, constituam dissentiunt per ex. In nam elitr assueverit.</p>

  <h3 class="abs" style="left:270px;top:61px;width:269px;text-align:center;font-weight:400;font-size:28px;letter-spacing:7px;color:#fff">OPTION B</h3>
  <p class="abs" style="left:270px;top:97px;width:269px;text-align:center;font-size:7.5px;color:#fff">Lorem Ipsum Dolor Sit Amet</p>
  <div class="abs" style="left:354px;top:109px;width:100px;height:1px;background:#ddd"></div>
  <p class="abs tiny" style="left:316px;top:129px;width:176px;text-align:center;color:#eee">Lorem ipsum dolor sit amet, ius exerci corpora eu. Per ne meis vocent iudicabit, in oratio graeci atomorum vim, vide habemus docendi ut eam. Cu dolor salutatus efficiendi nam.</p>
  <p class="abs tiny" style="left:316px;top:183px;width:176px;text-align:center;color:#eee">Nam dolor latine ornatus id, choro partiendo mei et. Idque facer vidisse id nec, constituam dissentiunt per ex. In nam elitr assueverit.</p>
  <div class="logo" style="left:370px;top:264px;font-size:19px">lum-vex, inc.</div>
</section>

<!-- Thank you -->
<section class="slide closing" style="left:615px;top:801px;width:540px;height:303px;background:var(--charcoal)">
  <div class="logo" style="left:0;top:52px;width:100%;text-align:center;font-size:30px">lum-vex, inc.</div>
  <h2 class="abs" style="left:0;top:110px;width:100%;text-align:center;color:#fff;font-weight:400;font-size:44px;line-height:38px">THANK<br>YOU</h2>
  <p class="abs" style="left:0;top:204px;width:100%;text-align:center;color:#8a0d12;font-size:9px">presented by <span style="font-size:11px">ALEX</span></p>
  <div class="badge" style="left:250px;top:232px;width:40px;height:40px"></div>
</section>

</body>
</html>
```